Highlight Document Over Image for Slide

We are seeking a graphic designer to overlay a news article on an image that pertains to the article, aiming for a stylish yet professional appearance. Given the limited resources, we encourage you to use your imagination and go beyond what basic tools like PowerPoint can offer.

```html
<!DOCTYPE html>
<html lang="en">
<head>
<meta charset="utf-8">
<title>Rule 20 – Introduction or Possession of Contraband Items</title>
<link href="https://fonts.googleapis.com/css2?family=Arimo:wght@400;700&family=Roboto+Condensed:wght@700&display=swap" rel="stylesheet">
<style>
  :root {
    --land-top: #8c7a57;
    --land-mid: #6f6a55;
    --water: #5e5f58;
    --water-deep: #575852;
    --band-dark: rgba(38, 38, 38, 0.92);
    --footer-band: rgba(98, 98, 98, 0.9);
    --text-white: #ffffff;
    --rule-line: #e6e6e6;
    --page-num: #c9c9c9;
  }
  * { margin: 0; padding: 0; box-sizing: border-box; }
  html, body { width: 1200px; height: 772px; overflow: hidden; background: var(--water); }
  .slide {
    position: relative;
    width: 1200px;
    height: 772px;
    overflow: hidden;
    font-family: "Arimo", Arial, sans-serif;
    color: var(--text-white);
  }
  .aerial-view {
    position: absolute;
    inset: 0;
    background:
      radial-gradient(ellipse 420px 300px at 480px 250px, #7d7a6c 0%, rgba(125,122,108,0) 100%),
      linear-gradient(170deg, var(--land-top) 0%, var(--land-mid) 38%, var(--water) 62%, var(--water-deep) 100%);
  }
  .footer-band {
    position: absolute;
    left: 0; right: 0;
    top: 690px; bottom: 0;
    background: var(--footer-band);
  }
  .title-band {
    position: absolute;
    left: 706px; top: 276px;
    width: 494px; height: 99px;
    background: var(--band-dark);
  }
  .rule-number {
    position: absolute;
    left: 730px; top: 284px;
    font-family: "Roboto Condensed", "Arial Narrow", sans-serif;
    font-weight: 700;
    font-size: 80px;
    line-height: 80px;
    letter-spacing: -1px;
  }
  .rule-title {
    position: absolute;
    left: 832px; top: 296px;
    font-family: "Roboto Condensed", "Arial Narrow", sans-serif;
    font-weight: 700;
    font-size: 25.5px;
    line-height: 29px;
    letter-spacing: 0.2px;
  }
  .rule-body {
    position: absolute;
    right: 37px; top: 383px;
    width: 560px;
    text-align: right;
  }
  .rule-lead {
    font-size: 24px;
    line-height: 30px;
  }
  .rule-items {
    font-family: "Roboto Condensed", "Arial Narrow", sans-serif;
    font-weight: 700;
    font-size: 33.5px;
    line-height: 37px;
    margin-top: 5px;
  }
  .rule-detail {
    position: absolute;
    right: 37px; top: 644px;
    width: 1060px;
    text-align: right;
    font-size: 18px;
    line-height: 24px;
  }
  .page-rule {
    position: absolute;
    left: 0; top: 750px;
    width: 1140px; height: 1px;
    background: var(--rule-line);
  }
  .page-number {
    position: absolute;
    right: 24px; top: 738px;
    font-size: 19px;
    color: var(--page-num);
  }
</style>
</head>
<body>
  <main class="slide">
    <div class="aerial-view" role="img" aria-label="Aerial satellite view of a waterfront correctional facility with surrounding roads, hills and bay water"></div>
    <div class="footer-band"></div>

    <div class="title-band"></div>
    <div class="rule-number">20</div>
    <h1 class="rule-title">INTRODUCTION OR POSSESSION<br>OF CONTRABAND ITEMS</h1>

    <section class="rule-body">
      <p class="rule-lead">Employees shall not introduce or<br>possess unauthorized items such as</p>
      <p class="rule-items">escape paraphernalia, weapons,<br>facsimiles of weapons, ammunition,<br>wireless communication devices,<br>cell phones, tobacco or<br>facsimiles of tobacco products</p>
    </section>

    <p class="rule-detail">(e.g. electronic vapor cigarettes), lighters or any other item not specifically authorized by PD 04.04.100 "Custody,<br>Security and Safety Systems (Exempt)", OP 04.04.100 "Gate Security" or facility operating procedure in any facility<br>where offenders are housed. Employees are responsible for any item in their</p>

    <div class="page-rule"></div>
    <div class="page-number">36</div>
  </main>
</body>
</html>
```